Letterhead and business card design

We have recently had a logo designed by brandnestly. now we need a corporate identity with business card and lettehead design.

Target Market(s)

law firms corporates

Industry/Entity Type

Business

Requirements
Should not have
• cheesy detecive stuff like magnifying glasses etxcc

```html
<!DOCTYPE html>
<html lang="en">
<head>
<meta charset="utf-8">
<title>Halvorsen &amp; Pryce — Stationery</title>
<link href="https://fonts.googleapis.com/css2?family=Questrial&display=swap" rel="stylesheet">
<style>
  :root {
    --bg: #ececec;
    --paper: #ffffff;
    --ink: #3a3a3a;
    --ink-soft: #6b6b6b;
    --rule: #9a9a9a;
    --silver-light: #b9bcbb;
    --silver-dark: #7d8180;
    --ink-blue: #2f5fae;
    --on-silver: #f4f4f4;
  }
  * { box-sizing: border-box; margin: 0; padding: 0; }
  html, body { width: 1200px; height: 979px; overflow: hidden; }
  body {
    background: var(--bg);
    font-family: "Questrial", "Century Gothic", sans-serif;
    color: var(--ink);
    position: relative;
  }

  /* Company name block */
  .masthead { text-align: center; }
  .company-name {
    display: block;
    font-family: "Questrial", sans-serif;
    font-weight: 400;
    color: var(--ink-soft);
    letter-spacing: 0.06em;
    line-height: 1.1;
  }
  .services {
    display: block;
    color: var(--ink-soft);
    margin-top: 5px;
    letter-spacing: 0.03em;
  }

  /* Letterhead */
  .letterhead {
    position: absolute;
    left: 70px; top: 70px;
    width: 590px; height: 835px;
    background: var(--paper);
    box-shadow: 0 2px 10px rgba(0,0,0,.12);
    padding: 60px 62px 0;
  }
  .letterhead .masthead { margin-bottom: 62px; }
  .letterhead .company-name { font-size: 26px; }
  .letterhead .services { font-size: 11px; }
  .salutation { font-size: 10px; font-weight: bold; margin-bottom: 12px; }
  .letter-body p {
    font-size: 9.2px; line-height: 1.55; text-align: justify;
    margin-bottom: 13px; color: var(--ink);
  }
  .signoff {
    margin-top: 18px;
    margin-left: 300px;
    font-size: 9px;
  }
  .signature {
    display: block; width: 150px; height: 46px;
    margin: 8px 0 6px 8px;
  }
  .signatory { font-size: 9px; line-height: 1.4; text-align: right; width: 160px; }
  .letter-footer {
    position: absolute; left: 62px; right: 62px; bottom: 40px;
    text-align: center; color: var(--ink-soft);
  }
  .letter-footer .rule { border-top: 1px solid var(--rule); margin-bottom: 8px; }
  .letter-footer .address { font-size: 8.5px; margin-bottom: 3px; }
  .letter-footer .contact { font-size: 8.5px; margin-bottom: 8px; }
  .letter-footer .contact b { color: var(--ink); }
  .letter-footer .legal { font-size: 6.8px; line-height: 1.4; border-top: 1px solid var(--rule); padding-top: 6px; }

  /* Business cards */
  .card {
    position: absolute;
    width: 380px; height: 218px;
    box-shadow: 0 2px 8px rgba(0,0,0,.14);
  }
  .card .company-name { font-size: 21px; }
  .card .services { font-size: 9px; }

  .card-front { left: 740px; top: 640px; background: var(--paper); padding: 28px 24px 0; }
  .card-front .holder { text-align: center; margin-top: 22px; }
  .holder-name { font-size: 11px; font-weight: bold; letter-spacing: .04em; }
  .holder-role { font-size: 9px; color: var(--ink-soft); margin-top: 2px; }
  .card-front .card-contact {
    position: absolute; left: 18px; right: 18px; bottom: 16px;
    text-align: center; font-size: 7.8px; color: var(--ink-soft); line-height: 1.55;
  }
  .card-contact b { color: var(--ink); }

  .card-back {
    left: 740px; top: 370px;
    background: linear-gradient(160deg, var(--silver-light) 0%, #a3a7a6 45%, var(--silver-dark) 100%);
    padding: 44px 24px 0;
  }
  .card-back .company-name,
  .card-back .services { color: var(--on-silver); }
  .card-back .web {
    position: absolute; right: 24px; bottom: 22px;
    font-size: 8.5px; color: var(--on-silver); letter-spacing: .03em;
  }
</style>
</head>
<body>

<section class="letterhead">
  <header class="masthead">
    <span class="company-name">Halvorsen &amp; Pryce</span>
    <span class="services">Investigations · Security · Intelligence</span>
  </header>

  <p class="salutation">Dear sir / madame,</p>
  <div class="letter-body">
    <p>Lorem ipsum dolor sit amet, consectetur adipisicing elit, sed do eiusmod tempor incididunt ut labore et dolore magna aliqua. Ut enim ad minim veniam, quis nostrud exercitation ullamco laboris nisi ut aliquip ex ea commodo consequat. Duis aute irure dolor in reprehenderit in voluptate velit esse cillum dolore eu fugiat nulla pariatur. Excepteur sint occaecat cupidatat non proident, sunt in culpa qui officia deserunt mollit anim id est laborum. Lorem ipsum dolor sit amet, consectetur adipisicing elit, sed do eiusmod tempor incididunt ut labore et dolore magna aliqua. Ut enim ad minim veniam, quis nostrud exercitation ullamco laboris nisi ut aliquip ex ea commodo consequat. Duis aute irure dolor in reprehenderit in voluptate velit esse cillum dolore eu fugiat nulla pariatur. Excepteur sint occaecat cupidatat non proident, sunt in culpa qui officia deserunt mollit anim id est laborum.</p>
    <p>Lorem ipsum dolor sit amet, consectetur adipisicing elit, sed do eiusmod tempor incididunt ut labore et dolore magna aliqua. Ut enim ad minim veniam, quis nostrud exercitation ullamco laboris nisi ut aliquip ex ea commodo consequat. Duis aute irure dolor in reprehenderit in voluptate velit esse cillum dolore eu fugiat nulla pariatur. Excepteur sint occaecat cupidatat non proident, sunt in culpa qui officia deserunt mollit anim id est laborum.</p>
    <p>Lorem ipsum dolor sit amet, consectetur adipisicing elit, sed do eiusmod tempor incididunt ut labore et dolore magna aliqua. Ut enim ad minim veniam, quis nostrud exercitation ullamco laboris nisi ut aliquip ex ea commodo consequat. Duis aute irure dolor in reprehenderit in voluptate velit esse cillum dolore eu fugiat nulla pariatur. Excepteur sint occaecat cupidatat non proident, sunt in culpa qui officia deserunt mollit anim id est laborum.</p>
  </div>

  <div class="signoff">
    <p>Yours faithfully, <strong>HALVORSEN AND PRYCE</strong></p>
    <svg class="signature" viewBox="0 0 150 46" role="img" aria-label="Handwritten signature of the director">
      <rect x="0" y="8" width="150" height="30" rx="15" fill="var(--ink-blue)" opacity="0.12"/>
    </svg>
    <div class="signatory">Marcus Hale<br>Director</div>
  </div>

  <footer class="letter-footer">
    <div class="rule"></div>
    <p class="address">PO Box 318, Harbour Lane, Wellington, New Zealand</p>
    <p class="contact"><b>Tel:</b> +64 9 555 0142 · <b>Fax:</b> +64 9 555 0187 · <b>Email:</b> marcus@halvorsenpryce.co.nz · www.halvorsenpryce.co.nz</p>
    <p class="legal">Government Licensed Private Investigators (licence number 604318). Halvorsen and Pryce Investigations Limited have no more authority than that of an ordinary private citizen to require a reply to this correspondence.</p>
  </footer>
</section>

<section class="card card-back">
  <div class="masthead">
    <span class="company-name">Halvorsen &amp; Pryce</span>
    <span class="services">Investigations · Security · Intelligence</span>
  </div>
  <p class="web">www.halvorsenpryce.co.nz</p>
</section>

<section class="card card-front">
  <div class="masthead">
    <span class="company-name">Halvorsen &amp; Pryce</span>
    <span class="services">Investigations · Security · Intelligence</span>
  </div>
  <div class="holder">
    <p class="holder-name">MARCUS HALE</p>
    <p class="holder-role">Director</p>
  </div>
  <div class="card-contact">
    <p>PO Box 318, Harbour Lane, Wellington, New Zealand</p>
    <p><b>Tel:</b> +64 9 555 0142 · <b>Fax:</b> +64 9 555 0187 · <b>Email:</b> marcus@halvorsenpryce.co.nz</p>
  </div>
</section>

</body>
</html>
```